GlassHaven Artbook for Okanagan Region, British Columbia

Creating an art book: GlassHaven, for the Okanagan Wine Region in British Columbia, Canada. Would like smart, modern, clean and linear...cool, sexy urban, not ugly boring suburban... I need a cover that appeals to the wino in all of us! Title: GlassHaven -Marla Dovicki
Updates
Thank you all kindly for your efforts. I have added some files so that you can get a sense of my aesthetic...it's never easy trying to figure it out, is it? I will hopefully have dimensions of book soon...cheers, Marla
would anyone please design a giant wine bottle with the wine label that looks like a label but says glasshaven...just curious to see if it works as a design or not...thank you.
Target Market(s)
Designing this wine art book of quotes to wineries in Okanagan BC. Buyer is wine lover and tourist ready to spend his vacation bucks on this wonderful book!
Look and feel

```html
<!DOCTYPE html>
<html lang="en">
<head>
<meta charset="utf-8">
<title>GlassHaven — Marla Dovicki</title>
<link rel="stylesheet" href="https://fonts.googleapis.com/css2?family=Anton&family=Oswald:wght@500&display=swap">
<style>
  :root {
    --paper: #efe4cb;
    --paper-edge: #e2d2b2;
    --frame: rgba(214, 128, 78, 0.78);
    --wine-red: #d9574e;
    --bottle-brown: #7f5238;
    --bottle-teal: #86d1ad;
    --bottle-orange: #ee8020;
    --bottle-olive: #8b8656;
    --cream: #f2e3c4;
  }
  html, body {
    margin: 0;
    padding: 0;
    overflow: hidden;
    background: #ffffff;
  }
  .cover {
    position: relative;
    width: 938px;
    height: 1200px;
    overflow: hidden;
    background: radial-gradient(ellipse at 50% 48%, var(--paper) 55%, var(--paper-edge) 100%);
  }
  .cover__frame {
    position: absolute;
    inset: 0;
    border: 39px solid var(--frame);
    box-sizing: border-box;
    z-index: 3;
    pointer-events: none;
  }
  .bottle-row {
    position: absolute;
    left: 0;
    width: 938px;
    z-index: 1;
  }
  .bottle-row--top {
    top: 0;
    height: 414px;
    background: linear-gradient(90deg,
      var(--wine-red) 0%, var(--bottle-brown) 12%, var(--bottle-teal) 26%,
      var(--bottle-orange) 40%, var(--bottle-olive) 48%, var(--bottle-teal) 55%,
      var(--wine-red) 63%, var(--bottle-orange) 76%, var(--bottle-brown) 92%);
    -webkit-mask-image: linear-gradient(180deg, #000 55%, transparent 100%);
            mask-image: linear-gradient(180deg, #000 55%, transparent 100%);
    opacity: 0.9;
  }
  .bottle-row--bottom {
    bottom: 0;
    height: 520px;
    background: linear-gradient(90deg,
      var(--bottle-brown) 0%, var(--bottle-teal) 12%, var(--bottle-orange) 20%,
      var(--bottle-teal) 30%, var(--wine-red) 38%, var(--bottle-orange) 47%,
      var(--bottle-brown) 57%, var(--wine-red) 65%, var(--bottle-teal) 75%,
      var(--bottle-orange) 84%, var(--bottle-teal) 93%, var(--wine-red) 100%);
    -webkit-mask-image: linear-gradient(0deg, #000 60%, transparent 100%);
            mask-image: linear-gradient(0deg, #000 60%, transparent 100%);
    opacity: 0.9;
  }
  .cover__title {
    position: absolute;
    top: 440px;
    left: 0;
    width: 938px;
    margin: 0;
    text-align: center;
    font-family: "Anton", "Oswald", sans-serif;
    font-weight: 400;
    font-size: 176px;
    line-height: 1;
    letter-spacing: 2px;
    color: var(--wine-red);
    text-transform: uppercase;
    transform: scaleY(1.15);
    transform-origin: top center;
    text-shadow: 3px 3px 0 var(--cream), 6px 6px 0 var(--wine-red);
    z-index: 2;
  }
  .cover__author {
    position: absolute;
    top: 1030px;
    left: 0;
    width: 938px;
    margin: 0;
    text-align: center;
    font-family: "Oswald", sans-serif;
    font-weight: 500;
    font-size: 56px;
    line-height: 1;
    letter-spacing: 1px;
    color: var(--cream);
    text-transform: uppercase;
    z-index: 2;
  }
</style>
</head>
<body>
  <main class="cover">
    <div class="bottle-row bottle-row--top" role="img" aria-label="Row of overlapping upside-down wine bottle silhouettes in red, brown, teal, orange and olive"></div>
    <h1 class="cover__title">GlassHaven</h1>
    <div class="bottle-row bottle-row--bottom" role="img" aria-label="Row of overlapping upright wine bottle silhouettes in red, brown, teal, orange and olive"></div>
    <p class="cover__author">Marla Dovicki</p>
    <div class="cover__frame"></div>
  </main>
</body>
</html>
```